New LLC consulting company needs a business card design

I need a business card design for new company in Alexandria Virginia called TK Verdane Consulting LLC. The company is focused on consulting for defense and national security issues with expertise in nuclear and space topics. I would like to see designs that are simple and I am open to colors except for brown.

Target Market(s)

All businesses that are seeking consulting help

Industry/Entity Type

Consulting

Contact Information for Business Card

Name of company - TK Verdane Consulting LLC; name (Delia Pratt) President; email: prattdq47@mailvessa.com; Phone: 703-555-0142

Requirements
Must have
• The details described above
Nice to have
• I'm open to all ideas
Should not have
• No brown

```html
<!DOCTYPE html>
<html lang="en">
<head>
<meta charset="utf-8">
<title>Delia Pratt – TK Verdane Consulting LLC</title>
<link rel="stylesheet" href="https://fonts.googleapis.com/css2?family=Montserrat:wght@400;700&display=swap">
<style>
  :root {
    --page-bg: #e9e9e9;
    --card-bg: #ffffff;
    --ink-strong: #050505;
    --ink-soft: #2b2b2b;
    --rule: #111111;
  }
  html, body {
    margin: 0;
    padding: 0;
    width: 1200px;
    height: 1059px;
    overflow: hidden;
    background: var(--page-bg);
    font-family: "Montserrat", Arial, sans-serif;
  }
  .card {
    position: absolute;
    left: 234px;
    top: 321px;
    width: 732px;
    height: 418px;
    background: var(--card-bg);
    border-radius: 26px;
  }
  .identity {
    position: absolute;
    right: 421px;
    top: 172px;
    text-align: right;
  }
  .identity__name {
    margin: 0;
    font-weight: 700;
    font-size: 35px;
    line-height: 40px;
    color: var(--ink-strong);
    letter-spacing: 0.2px;
    white-space: nowrap;
  }
  .identity__title {
    margin: 2px 0 0;
    font-weight: 400;
    font-size: 19px;
    line-height: 24px;
    color: var(--ink-soft);
    letter-spacing: 0.5px;
    white-space: nowrap;
  }
  .divider {
    position: absolute;
    left: 347px;
    top: 172px;
    width: 2px;
    height: 74px;
    background: var(--rule);
  }
  .contacts {
    position: absolute;
    left: 385px;
    top: 181px;
    margin: 0;
    padding: 0;
    list-style: none;
  }
  .contacts__item {
    display: flex;
    align-items: center;
    height: 24px;
    margin-bottom: 10px;
    font-size: 18.5px;
    color: var(--ink-soft);
    letter-spacing: 0.4px;
    white-space: nowrap;
  }
  .contacts__icon {
    width: 17px;
    height: 17px;
    margin-right: 7px;
    flex-shrink: 0;
  }
  .company {
    position: absolute;
    left: 0;
    right: 0;
    bottom: 52px;
    margin: 0;
    text-align: center;
    font-weight: 700;
    font-size: 15px;
    line-height: 20px;
    letter-spacing: 3px;
    text-transform: uppercase;
    color: var(--ink-strong);
    white-space: nowrap;
  }
</style>
</head>
<body>
  <section class="card" aria-label="Business card for Delia Pratt, TK Verdane Consulting LLC">
    <div class="identity">
      <h1 class="identity__name">Delia Pratt</h1>
      <p class="identity__title">President</p>
    </div>
    <div class="divider"></div>
    <ul class="contacts">
      <li class="contacts__item">
        <svg class="contacts__icon" viewBox="0 0 24 24" aria-hidden="true">
          <rect x="2" y="6" width="20" height="13" fill="#111"/>
          <path d="M2 6 L12 13.5 L22 6" fill="none" stroke="#fff" stroke-width="1.6"/>
          <path d="M2 19 L9.5 12 M22 19 L14.5 12" fill="none" stroke="#fff" stroke-width="1.2"/>
        </svg>
        prattdq47@mailvessa.com
      </li>
      <li class="contacts__item">
        <svg class="contacts__icon" viewBox="0 0 24 24" aria-hidden="true">
          <path d="M6.6 10.8c1.4 2.8 3.8 5.1 6.6 6.6l2.2-2.2c.3-.3.7-.4 1-.2 1.1.4 2.3.6 3.6.6.6 0 1 .4 1 1V20c0 .6-.4 1-1 1C10.6 21 3 13.4 3 4c0-.6.4-1 1-1h3.5c.6 0 1 .4 1 1 0 1.3.2 2.5.6 3.6.1.3 0 .7-.2 1z" fill="#111"/>
          <path d="M14 2.5a7.5 7.5 0 0 1 7.5 7.5M14 6a4 4 0 0 1 4 4" fill="none" stroke="#111" stroke-width="1.8"/>
        </svg>
        703-555-0142
      </li>
    </ul>
    <p class="company">TK Verdane Consulting LLC</p>
  </section>
</body>
</html>
```